Business card design

I already have the logo design completed and am requiring business card design and layout utilising the logo. I require a front and back design.

We are an executive recruitment company so we are looking at full colour, high finish in a reasonably conservative structure.

Reason: will be provide ai template

Target Market(s)

Senior Management 35-60 age bracket

Industry/Entity Type

Business

Requirements
Must have
• Peter Welling
• Director
• 238 Morrow Tce, Kelvin Grove QLD 4059
• Ph: 07 3628 4190 Mob: 0418527306
• peter@voltinapartners.com.au
• www.voltinapartners.com.au
Nice to have
• Ideally full colour,
Should not have
• cheap looking

```html
<!DOCTYPE html>
<html lang="en">
<head>
<meta charset="utf-8">
<title>Voltina Partners – Business Card</title>
<link rel="stylesheet" href="https://fonts.googleapis.com/css2?family=Open+Sans:wght@400;600;700&display=swap">
<style>
  :root {
    --backdrop: #d3d3d3;
    --paper: #ffffff;
    --navy: #173a6a;
    --navy-light: #1d4c84;
    --navy-deep: #0e2650;
    --ink-grey: #555a60;
    --soft-grey: #9a9ea3;
    --white: #ffffff;
  }
  * { box-sizing: border-box; margin: 0; padding: 0; }
  html, body {
    width: 1105px;
    height: 1200px;
    overflow: hidden;
    background: var(--backdrop);
    font-family: "Open Sans", Arial, sans-serif;
  }
  .sheet {
    position: relative;
    width: 1105px;
    height: 1200px;
  }
  .card {
    position: absolute;
    left: 112px;
    width: 880px;
    height: 489px;
    overflow: hidden;
    box-shadow: 0 4px 14px rgba(0,0,0,0.12);
  }
  .card--front { top: 80px; background: var(--paper); }
  .card--back {
    top: 630px;
    background: linear-gradient(160deg, var(--navy-light) 0%, var(--navy) 45%, var(--navy-deep) 100%);
  }

  .brand {
    position: absolute;
    display: flex;
    align-items: center;
    gap: 22px;
  }
  .brand__dot {
    width: 64px;
    height: 64px;
    border-radius: 50%;
    flex: none;
  }
  .brand__name {
    font-weight: 700;
    font-size: 38px;
    letter-spacing: 2px;
    white-space: nowrap;
  }
  .card--front .brand { left: 70px; top: 70px; }
  .card--front .brand__dot { background: var(--navy); }
  .card--front .brand__name { color: var(--navy); }

  .card--back .brand {
    left: 50%;
    top: 50%;
    transform: translate(-50%, -58%);
  }
  .card--back .brand__dot { background: var(--white); }
  .card--back .brand__name { color: var(--white); }

  .person {
    position: absolute;
    left: 70px;
    top: 252px;
  }
  .person__name {
    font-weight: 700;
    font-size: 35px;
    color: var(--navy);
    line-height: 1.2;
  }
  .person__role {
    font-size: 29px;
    color: var(--ink-grey);
    line-height: 1.2;
  }

  .contact {
    position: absolute;
    left: 500px;
    top: 262px;
    list-style: none;
    font-size: 22px;
    line-height: 38px;
    color: var(--soft-grey);
    white-space: nowrap;
  }

  .website {
    position: absolute;
    left: 0;
    right: 0;
    bottom: 24px;
    text-align: center;
    font-weight: 600;
    font-size: 30px;
    color: var(--white);
    letter-spacing: 0.5px;
  }
</style>
</head>
<body>
  <main class="sheet">
    <section class="card card--front" aria-label="Business card front">
      <div class="brand">
        <span class="brand__dot"></span>
        <span class="brand__name">VOLTINA PARTNERS</span>
      </div>
      <div class="person">
        <p class="person__name">Peter Welling</p>
        <p class="person__role">Director</p>
      </div>
      <ul class="contact">
        <li>238 Morrow Tce,</li>
        <li>Kelvin Grove QLD 4059</li>
        <li>P: 07 3628 4190</li>
        <li>M: 0418527306</li>
        <li>peter@voltinapartners.com.au</li>
      </ul>
    </section>

    <section class="card card--back" aria-label="Business card back">
      <div class="brand">
        <span class="brand__dot"></span>
        <span class="brand__name">VOLTINA PARTNERS</span>
      </div>
      <p class="website">www.voltinapartners.com.au</p>
    </section>
  </main>
</body>
</html>
```